Tradeshow Booth Design

Clean background, some variance of kelly green in the colors - see image for text - maybe an image with people or nice modern homes...

Target Market(s)

Mortgage Professionals

Industry/Entity Type

Mortgage Lender

Font styles to use
Serif
Sans Serif

Colors
9bcb3c
cadf82

Requirements
Must have
• Logo, the words on the image

```html
<!DOCTYPE html>
<html lang="en">
<head>
<meta charset="utf-8">
<title>Birchline Lending – Tradeshow Booth</title>
<link rel="stylesheet" href="https://fonts.googleapis.com/css2?family=Montserrat:wght@300;600;800&display=swap">
<style>
  :root {
    --kelly-dark: #1e6b39;
    --kelly-mid: #8cbd5c;
    --leaf-light: #b8d87f;
    --rule-grey: #b4b4b4;
    --floor-grey: #e6e7e8;
    --floor-edge: #c8c8c8;
    --trim-red: #e0403a;
    --white: #ffffff;
  }
  * { margin: 0; padding: 0; box-sizing: border-box; }
  html, body { width: 1200px; height: 800px; overflow: hidden; background: var(--white); }
  body { font-family: "Montserrat", Arial, sans-serif; }

  .booth { position: relative; width: 1200px; height: 800px; overflow: hidden; background: var(--white); }
  .booth__backdrop { position: absolute; inset: 0; }

  .brand {
    position: absolute; left: 310px; top: 60px;
    display: flex; align-items: center; gap: 26px;
  }
  .brand__mark { width: 88px; height: 88px; border-radius: 50%; background: var(--white); }
  .brand__name {
    font-weight: 600; font-size: 46px; letter-spacing: 1px;
    color: var(--white); line-height: 1; white-space: nowrap;
  }

  .tagline-flex {
    position: absolute; left: 729px; width: 266px; top: 200px;
    text-align: right; line-height: 1;
  }
  .tagline-flex__bold { display: block; font-weight: 800; font-size: 31px; color: var(--leaf-light); letter-spacing: 1px; }
  .tagline-flex__light { display: block; font-weight: 300; font-size: 41px; color: var(--leaf-light); margin-top: 4px; }
  .tagline-flex__rule { height: 2px; background: var(--rule-grey); margin-top: 8px; }

  .headline { position: absolute; left: 232px; top: 328px; line-height: 1; }
  .headline__lead { display: block; font-weight: 800; font-size: 48px; color: var(--kelly-dark); }
  .headline__main { display: block; font-weight: 300; font-size: 62px; color: var(--kelly-dark); margin-top: 2px; white-space: nowrap; }
  .headline__for { font-size: 30px; margin-left: 8px; }
  .headline__rule { width: 440px; height: 2px; background: var(--rule-grey); margin-top: 10px; }
  .headline__audience {
    display: block; font-weight: 800; font-size: 29px; color: var(--leaf-light);
    margin-top: 14px; line-height: 1.25; letter-spacing: 0.5px;
  }

  .floor { position: absolute; left: 0; right: 0; top: 763px; bottom: 0; background: var(--floor-grey); border-top: 5px solid var(--floor-edge); }
  .trim { position: absolute; top: 0; bottom: 0; width: 0; border-left: 1px dashed var(--trim-red); }
  .trim--left { left: 155px; }
  .trim--right { left: 1045px; }
</style>
</head>
<body>
<main class="booth">
  <svg class="booth__backdrop" width="1200" height="800" viewBox="0 0 1200 800" aria-hidden="true">
    <defs>
      <linearGradient id="swoosh-shadow" x1="0" y1="0" x2="0" y2="1">
        <stop offset="0" stop-color="#000" stop-opacity="0.12"/>
        <stop offset="1" stop-color="#000" stop-opacity="0"/>
      </linearGradient>
    </defs>
    <path d="M0,485 C250,285 600,168 1000,158 C600,170 250,290 0,485 Z" fill="url(#swoosh-shadow)"/>
    <path class="swoosh-light" d="M0,474 C250,270 600,155 1000,148 C600,150 250,240 0,425 Z" fill="var(--leaf-light)"/>
    <path class="swoosh-mid" d="M0,448 C250,255 600,152 1000,147 C600,150 250,245 0,436 Z" fill="var(--kelly-mid)" opacity="0.7"/>
    <path class="header-band" d="M0,0 H1200 V177 C1130,160 1070,150 1000,146 C600,146 250,235 0,425 Z" fill="var(--kelly-dark)"/>
    <circle class="decor-mark" cx="882" cy="650" r="105" fill="var(--leaf-light)"/>
  </svg>

  <div class="brand">
    <span class="brand__mark"></span>
    <span class="brand__name">BIRCHLINE LENDING</span>
  </div>

  <div class="tagline-flex">
    <span class="tagline-flex__bold">FLEXIBLE</span>
    <span class="tagline-flex__light">GUIDELINES</span>
    <div class="tagline-flex__rule"></div>
  </div>

  <div class="headline">
    <span class="headline__lead">Innovative</span>
    <span class="headline__main">SOLUTIONS<span class="headline__for">for</span></span>
    <div class="headline__rule"></div>
    <span class="headline__audience">NON-TRADITIONAL<br>BORROWERS</span>
  </div>

  <div class="floor"></div>
  <div class="trim trim--left"></div>
  <div class="trim trim--right"></div>
</main>
</body>
</html>
```